Hop Along Days campaign: promoting kids play in the UK - Website Redesign

Hop Along Days is a national UK campaign that promotes the value of play for children. The current website is live at http://www.hopalongdays.co.uk. This website has been live for 4 years and now needs to be redesigned. The target audience is parents of young children up to the age of 12.

The current site was designed with a series of old adverts in mind. Here is an example of an old advert: http://vidshare.example/qR7tLm2XwZa

Criticisms of existing site:
The design represented the adverts too closely. The result was a website that mirrors the adverts rather than complements them.
The color scheme is too dark.
Text-heavy pages (e.g. http://www.hopalongdays.co.uk/fun.php) are dull and not FUN!

New site
We have recently had a series of new video adverts produced:
advert 1: http://vidshare.example/hB4nVc8JsPe
advert 2: http://vidshare.example/KgW3rTy9DuM
advert 3: http://vidshare.example/zA5oEi1HbNq

The new site should be cleaner and brighter than the existing site, possibly with a white background using graphics, fonts and advert characters (see attached character graphics files) to add the element of fun and play.

The homepage should include:
1. Hop Along Days logo (attached)
2. Social Media links (visible on all pages of the site) – Chatterbook, Chirpline, ClipVault
3. Link to the HopAlongDays app page of the site (visible on all pages)
4. Image/video placeholder that the user can scroll through, view full-size images and play videos.
5. Text area to hold approximately 100 words describing the purpose of the campaign
6. Site footer to contain the same information as on the existing site along with the Northern Games & Crafts Guild logo (attached)

Site structure:
One change to the site structure… the “Brought to you by” menu item will be removed from the top-level menu.

General:
Some pages on the existing site are quite text-heavy, we would like to break up text on these pages in some way. Graphical division of paragraphs, use of advert characters?

Please note that all attached graphics file are the property of the Northern Games & Crafts Guild and must only be used for the purpose of this project.

```html
<!DOCTYPE html>
<html lang="en">
<head>
<meta charset="utf-8">
<title>Hop Along Days</title>
<link href="https://fonts.googleapis.com/css2?family=Fredoka:wght@600&family=Source+Sans+3:wght@400;600;700&display=swap" rel="stylesheet">
<style>
:root{
  --backdrop:#ececec;
  --page:#ffffff;
  --hero:#2aa9cf;
  --nav-orange:#e9ad2c;
  --nav-purple:#5b3f98;
  --nav-sky:#5ab4e5;
  --nav-yellow:#e8cf2a;
  --nav-pink:#dc5a78;
  --headline:#f5df2e;
  --ink:#2b2b2b;
  --accent:#4ab8d8;
  --meta-blue:#2aa0c8;
  --meta-deep:#2767b8;
  --views:#d0202a;
  --app-green:#b7d247;
  --app-edge:#9ab83a;
  --cta-pink:#e0466e;
  --frame:#9fb3b8;
  --footer-text:#a7a7a7;
  --social:#1a8fd6;
  --brand:#5b3f98;
  --leaf:#8fb845;
  --leaf-dark:#5f8c2e;
  --board:#f4efe3;
  --sky-pink:#f08aa6;
}
*{margin:0;padding:0;box-sizing:border-box}
a{text-decoration:none}
html,body{width:1200px;height:934px;overflow:hidden;background:var(--backdrop)}
.stage{position:relative;width:1399px;height:1090px;transform:scale(0.85775);transform-origin:0 0;font-family:"Source Sans 3",Arial,sans-serif;color:var(--ink)}
.page{position:absolute;left:200px;top:0;width:1000px;height:1090px;background:var(--page)}
.abs{position:absolute}

.brand{left:262px;top:42px;display:flex;align-items:center;gap:10px;font-family:"Fredoka",sans-serif;font-weight:600;font-size:30px;color:var(--brand);line-height:1}
.brand-dot{width:22px;height:22px;border-radius:50%;background:var(--nav-orange)}

.social{left:1000px;top:27px;display:flex;gap:12px;font-size:11px;font-weight:700;color:var(--social)}
.social a{color:inherit;display:flex;align-items:center;gap:4px}
.social i{display:block;width:22px;height:22px;border-radius:50%;background:var(--social)}

.main-nav{left:553px;top:76px;display:flex;height:45px}
.main-nav a{width:129px;margin-right:1px;display:flex;align-items:center;justify-content:center;color:#fff;font:bold 13px Arial,sans-serif;text-shadow:0 1px 1px rgba(0,0,0,.25)}

.hero{left:200px;top:122px;width:1000px;height:302px;background:var(--hero)}
.player{left:272px;top:135px;width:500px;height:270px;background:#fff;padding:6px}
.scene{background:
  radial-gradient(ellipse 28% 45% at 50% 48%,var(--board) 0 70%,transparent 100%),
  radial-gradient(ellipse 22% 18% at 40% 8%,var(--sky-pink) 0 40%,transparent 100%),
  radial-gradient(ellipse 35% 50% at 12% 30%,var(--leaf-dark) 0 30%,transparent 100%),
  radial-gradient(ellipse 30% 40% at 90% 25%,#cfe0a0 0 30%,transparent 100%),
  radial-gradient(ellipse 50% 30% at 50% 100%,#3d6bb0 0 20%,transparent 100%),
  linear-gradient(180deg,#b4cf6a,var(--leaf) 60%,#6f9a3a)}
.player-media{width:100%;height:100%}
.play-btn{left:493px;top:243px;width:60px;height:56px;border-radius:8px;background:rgba(210,210,210,.8)}
.hero-title{left:820px;top:160px;font-family:"Fredoka",sans-serif;font-weight:600;font-size:50px;line-height:56px;color:var(--headline);text-shadow:1px 2px 2px rgba(0,0,0,.2)}
.hero-title .last{color:var(--nav-orange)}
.hero-copy{left:820px;top:290px;width:345px;font:bold 10px/22px Arial,sans-serif;color:#fff}

.thumb{top:440px;width:140px;height:83px;border:3px solid var(--frame)}
.arrow{top:470px}
.app{left:824px;top:432px;width:293px;height:122px;background:var(--app-green);border:1px solid var(--app-edge)}
.phone{left:860px;top:437px;width:55px;height:113px;border-radius:9px;background:#111}
.phone-screen{left:866px;top:452px;width:43px;height:80px;background:#fff}
.phone-start{left:866px;top:514px;width:43px;text-align:center;font:bold 8px Arial,sans-serif;color:#333}
.phone-home{left:882px;top:537px;width:10px;height:10px;border-radius:50%;border:1px solid #777}
.app-title{left:935px;top:450px;width:160px;text-align:center;font:bold 25px/28px Arial,sans-serif;color:#fff;text-shadow:0 1px 2px rgba(0,0,0,.2)}
.app-cta{left:944px;top:519px;width:136px;height:26px;background:var(--cta-pink);border-radius:2px;color:#fff;font:bold 18px/26px Arial,sans-serif;text-align:center}

.feed-head{top:580px;display:flex;align-items:center;gap:14px}
.feed-title{font-size:22px;font-weight:400;color:var(--ink);white-space:nowrap;line-height:26px}
.feed-title span{color:var(--accent)}
.dots{flex:1;border-top:2px dotted #c8c8c8;margin-top:4px}

.feed-item{width:330px;height:70px}
.feed-pic{position:absolute;left:0;top:0;width:60px;height:55px;border:1px solid #bbb;background:
  radial-gradient(circle at 45% 55%,#e0b592 0 22%,transparent 40%),
  linear-gradient(135deg,#5d4a38,#8a7258 50%,#c9a27a)}
.feed-pic.warm{background:
  radial-gradient(circle at 45% 50%,#f3d9b8 0 22%,transparent 42%),
  linear-gradient(135deg,#e0a35a,#f7e3c4 50%,#b9773a)}
.feed-pic.stage-pic{background:
  radial-gradient(ellipse 30% 25% at 50% 62%,#7fa6e8 0 40%,transparent 100%),
  linear-gradient(180deg,#e0702a,#a33a14 45%,#2a120c)}
.feed-text{position:absolute;left:75px;top:-2px;width:200px;font-size:12px;line-height:16px}
.feed-meta{position:absolute;left:75px;top:53px;width:180px;font-size:10px;color:var(--meta-blue)}
.feed-meta .who{position:absolute;left:152px}
.deep .feed-meta{color:var(--meta-deep)}
.clip-pic{position:absolute;left:0;top:0;width:100px;height:55px;border:1px solid #bbb}
.clip-text{position:absolute;left:118px;top:-2px;width:145px;font-size:12px;line-height:16px}
.clip-views{position:absolute;left:118px;top:42px;font-size:10px;color:var(--views)}
.btn{top:885px;width:65px;height:13px;font:10px/13px Arial,sans-serif;color:#fff;text-align:center}

.rule{left:222px;top:964px;width:936px;border-top:1px solid #999}
.guild{left:262px;top:994px;display:flex;align-items:center;gap:8px;width:130px;font-size:13px;font-weight:700;line-height:17px;color:var(--ink)}
.guild i{flex:none;width:16px;height:16px;border-radius:50%;background:#c8302c}
.foot-nav{top:992px;font:bold 12.5px Arial,sans-serif;color:var(--footer-text)}
.foot-line{left:457px;width:600px;text-align:center;font:bold 12.5px Arial,sans-serif;color:var(--footer-text)}
</style>
</head>
<body>
<div class="stage">
  <div class="page"></div>

  <header>
    <div class="abs brand"><span class="brand-dot"></span>Hop Along Days</div>
    <nav class="abs social" aria-label="Social links">
      <a href="#"><i></i>Linkwell</a><a href="#"><i></i>Chatterbook</a><a href="#"><i></i>Chirpline</a>
    </nav>
    <nav class="abs main-nav">
      <a href="#" style="background:var(--nav-orange)">Play Right Now</a>
      <a href="#" style="background:var(--nav-purple)">Get Involved</a>
      <a href="#" style="background:var(--nav-sky)">WhyPlay</a>
      <a href="#" style="background:var(--nav-yellow)">Fun Forever</a>
      <a href="#" style="background:var(--nav-pink)">Resourcrs</a>
    </nav>
  </header>

  <section>
    <div class="abs hero"></div>
    <div class="abs player"><div class="player-media scene" role="img" aria-label="Video still: illustrated children in a leafy park beside a signboard"></div></div>
    <div class="abs play-btn"><svg width="60" height="56" viewBox="0 0 60 56"><path d="M25 18 L37 28 L25 38 Z" fill="#333"/></svg></div>
    <h1 class="abs hero-title">HOP ALONG<br><span class="last">DAYS</span></h1>
    <p class="abs hero-copy">Hop Along Days Ambassador Dr Helena Marsh explains the importance of engaging children in physical activity and the body image rock out her blog link</p>
  </section>

  <section>
    <svg class="abs arrow" style="left:272px" width="18" height="24" viewBox="0 0 18 24"><path d="M14 3 L5 12 L14 21" fill="none" stroke="#2aa9cf" stroke-width="4"/></svg>
    <div class="abs thumb" style="left:297px;background:radial-gradient(ellipse 40% 35% at 55% 55%,#c9a6d8 0 25%,transparent 100%),linear-gradient(180deg,#fbf8f1,#efe6d2)" role="img" aria-label="Thumbnail: campaign signboard"></div>
    <div class="abs thumb" style="left:447px;background:radial-gradient(ellipse 30% 40% at 35% 55%,#f1c9a8 0 30%,transparent 100%),radial-gradient(ellipse 40% 40% at 70% 50%,var(--board) 0 50%,transparent 100%),linear-gradient(135deg,var(--leaf-dark),var(--leaf))" role="img" aria-label="Thumbnail: illustrated girl among leaves"></div>
    <div class="abs thumb" style="left:597px" role="img" aria-label="Thumbnail: children beside signboard"><div class="scene" style="width:100%;height:100%"></div></div>
    <svg class="abs arrow" style="left:746px" width="18" height="24" viewBox="0 0 18 24"><path d="M4 3 L13 12 L4 21" fill="none" stroke="#2aa9cf" stroke-width="4"/></svg>

    <div class="abs app"></div>
    <div class="abs phone"></div>
    <div class="abs phone-screen"></div>
    <div class="abs phone-start">START</div>
    <div class="abs phone-home"></div>
    <div class="abs app-title">APP<br>AVAILABLE</div>
    <a class="abs app-cta" href="#">CLICK HERE</a>
  </section>

  <section>
    <div class="abs feed-head" style="left:220px;width:272px"><h2 class="feed-title">Chirpline <span>Feeds</span></h2><span class="dots"></span></div>
    <div class="abs feed-item" style="left:223px;top:630px"><div class="feed-pic" role="img" aria-label="Profile photo"></div><p class="feed-text">Donec luctus nisl in nibh ultricies quis convallis justo convallis. Fusce mattis mauris id enim.</p><div class="feed-meta">2-days ago<span class="who">mery/</span></div></div>
    <div class="abs feed-item" style="left:223px;top:714px"><div class="feed-pic warm" role="img" aria-label="Profile photo"></div><p class="feed-text">Donec luctus nisl in nibh ultricies quis convallis justo convallis. Fusce mattis mauris id enim.</p><div class="feed-meta">2-days ago<span class="who">mery/</span></div></div>
    <div class="abs feed-item" style="left:223px;top:798px"><div class="feed-pic stage-pic" role="img" aria-label="Photo of a lit theatre stage"></div><p class="feed-text">Donec luctus nisl in nibh ultricies quis convallis justo convallis. Fusce mattis mauris id enim.</p><div class="feed-meta">2-days ago<span class="who">mery/</span></div></div>
    <a class="abs btn" href="#" style="left:414px;background:#7cc9dd">Read More</a>

    <div class="abs feed-head" style="left:555px;width:272px"><h2 class="feed-title">Chatterbook <span>Feeds</span></h2><span class="dots"></span></div>
    <div class="abs feed-item deep" style="left:558px;top:630px"><div class="feed-pic" role="img" aria-label="Profile photo"></div><p class="feed-text">Donec luctus nisl in nibh ultricies quis convallis justo convallis. Fusce mattis mauris id enim.</p><div class="feed-meta">2-days ago</div></div>
    <div class="abs feed-item deep" style="left:558px;top:714px"><div class="feed-pic warm" role="img" aria-label="Profile photo"></div><p class="feed-text">Donec luctus nisl in nibh ultricies quis convallis justo convallis. Fusce mattis mauris id enim.</p><div class="feed-meta">2-days ago</div></div>
    <div class="abs feed-item deep" style="left:558px;top:798px"><div class="feed-pic stage-pic" role="img" aria-label="Photo of a lit theatre stage"></div><p class="feed-text">Donec luctus nisl in nibh ultricies quis convallis justo convallis. Fusce mattis mauris id enim.</p><div class="feed-meta">2-days ago</div></div>
    <a class="abs btn" href="#" style="left:749px;background:#2f5fb3">Read More</a>

    <div class="abs feed-head" style="left:886px;width:272px"><h2 class="feed-title">ClipVault</h2><span class="dots" style="margin-left:50px"></span></div>
    <div class="abs feed-item" style="left:889px;top:630px"><div class="clip-pic scene" role="img" aria-label="Video thumbnail: campaign advert"></div><p class="clip-text">Donec luctus nisl in nibh ultricies quis convallis justo</p><div class="clip-views">1200/ vies</div></div>
    <div class="abs feed-item" style="left:889px;top:718px"><div class="clip-pic scene" role="img" aria-label="Video thumbnail: campaign advert"></div><p class="clip-text">Donec luctus nisl in nibh ultricies quis convallis justo</p><div class="clip-views">1200/ vies</div></div>
    <div class="abs feed-item" style="left:889px;top:800px"><div class="clip-pic scene" role="img" aria-label="Video thumbnail: campaign advert"></div><p class="clip-text">Donec luctus nisl in nibh ultricies quis convallis justo</p><div class="clip-views">1200/ vies</div></div>
    <a class="abs btn" href="#" style="left:1080px;background:#7cc9dd">More videos</a>
  </section>

  <footer>
    <div class="abs rule"></div>
    <div class="abs guild"><i></i><span>Northern Games &amp; Crafts Guild</span></div>
    <span class="abs foot-nav" style="left:470px">Play Right Now</span>
    <span class="abs foot-nav" style="left:581px">|</span>
    <span class="abs foot-nav" style="left:611px">Get Involved</span>
    <span class="abs foot-nav" style="left:721px">|</span>
    <span class="abs foot-nav" style="left:755px">WhyPlay</span>
    <span class="abs foot-nav" style="left:831px">|</span>
    <span class="abs foot-nav" style="left:865px">Fun Forever</span>
    <span class="abs foot-nav" style="left:951px">|</span>
    <span class="abs foot-nav" style="left:988px">Resourcrs</span>
    <div class="abs foot-line" style="top:1016px">Privacy Policy &nbsp;| Terms</div>
    <div class="abs foot-line" style="top:1039px">Copyright © 2014 hopalongdays.co.uk. All Rights Reserved.</div>
  </footer>
</div>
</body>
</html>
```